STAND OUT BUSINESS CARD REQUIRED

I would like a business card that is going to be different and stand out!

Target Market(s)

Residential market, adults from 28yrs on

Industry/Entity Type

Electrician

Requirements
Must have
• Business name
• my name
• phone number
• email
• web address
• license no.
• abn
• fax no
• logo
Nice to have
• Extra info:
• FREE quotes
• Fixed pricing
• On time guarantee
• Life time labour Guarantee

```html
<!DOCTYPE html>
<html lang="en">
<head>
<meta charset="utf-8">
<title>Spark Ready Electrical – Business Card</title>
<link href="https://fonts.googleapis.com/css2?family=Arimo:wght@400;700&display=swap" rel="stylesheet">
<style>
  :root{
    --page:#ffffff;
    --ink:#000000;
    --orange:#f7941d;
    --orange-deep:#ee7a12;
    --yellow:#ffd23a;
    --dark:#141213;
    --dark-mid:#2a2728;
    --brand:#4a2a10;
    --white:#ffffff;
    --muted:#6f6a66;
    --gold:#e2b53a;
    --gold-light:#ffe68a;
    --gold-deep:#a87612;
  }
  *{margin:0;padding:0;box-sizing:border-box}
  html,body{width:1200px;height:873px;overflow:hidden;background:var(--page)}
  body{position:relative;font-family:"Arimo",Arial,sans-serif}

  .side-label{
    position:absolute;font-weight:700;font-size:44px;color:var(--ink);
    transform:rotate(-90deg);transform-origin:left top;white-space:nowrap;
  }
  .side-label--front{left:14px;top:240px}
  .side-label--back{left:578px;top:240px}

  .card{position:absolute;top:36px;width:480px;height:800px;overflow:hidden}
  .card--front{left:86px;background:radial-gradient(circle at 50% 22%,var(--yellow) 0%,var(--orange) 45%,var(--orange-deep) 100%)}
  .card--back{left:636px;background:radial-gradient(ellipse at 50% 50%,var(--dark-mid) 0%,var(--dark) 75%)}

  .mascot{
    position:absolute;left:135px;top:10px;width:220px;height:215px;border-radius:50%;
    background:radial-gradient(circle at 50% 45%,rgba(70,150,60,.85) 0%,rgba(200,60,40,.55) 55%,rgba(247,148,29,0) 75%);
  }
  .dome{position:absolute;left:0;top:0;width:480px;height:800px}
  .dome path{fill:var(--dark)}

  .brand-name{
    position:absolute;left:0;width:480px;top:232px;text-align:center;
    font-weight:700;font-size:36px;line-height:38px;color:var(--brand);letter-spacing:.5px;
  }
  .brand-name small{display:block;font-size:18px;line-height:22px;margin-top:2px}

  .name-tab{
    position:absolute;left:0;top:428px;width:320px;height:36px;background:var(--orange);
    clip-path:polygon(0 0,100% 0,88% 100%,0 100%);
  }
  .person-name{position:absolute;left:36px;top:433px;font-weight:700;font-size:27px;color:var(--ink)}
  .person-role{position:absolute;left:36px;top:467px;font-weight:700;font-size:18px;color:var(--orange);letter-spacing:.5px}

  .contacts{position:absolute;left:36px;top:533px;list-style:none}
  .contacts li{font-size:21px;line-height:33px;color:var(--white);font-weight:700}
  .contacts .label{color:var(--orange);font-weight:400;font-size:23px}

  .legal{position:absolute;left:36px;top:708px;font-size:16px;line-height:24px;color:var(--muted);font-weight:700}

  .feature{position:absolute;left:0;width:480px;text-align:center}
  .feature--pricing{top:66px}
  .feature--time{top:297px}
  .feature--labour{top:533px}
  .seal{
    width:132px;height:132px;margin:0 auto;border-radius:50%;
    background:radial-gradient(circle at 40% 35%,var(--gold-light) 0%,var(--gold) 50%,var(--gold-deep) 100%);
  }
  .feature-title{margin-top:30px;font-size:22px;line-height:31px;color:var(--gold)}
</style>
</head>
<body>
  <div class="side-label side-label--front">Side 1</div>
  <div class="side-label side-label--back">Side 2</div>

  <section class="card card--front">
    <div class="mascot" role="img" aria-label="Superhero electrician mascot holding a light bulb"></div>
    <svg class="dome" viewBox="0 0 480 800" aria-hidden="true">
      <path d="M0,415 Q240,320 480,355 L480,800 L0,800 Z"/>
    </svg>
    <div class="brand-name">SPARK READY<br>ELECTRICAL<small>Pty Ltd</small></div>

    <div class="name-tab"></div>
    <div class="person-name">Liam Carter</div>
    <div class="person-role">DIRECTOR</div>

    <ul class="contacts">
      <li><span class="label">phone:</span> 0400 555 123</li>
      <li><span class="label">fax:</span> 02 9000 5555</li>
      <li><span class="label">email:</span> info@sparkready.com.au</li>
      <li><span class="label">web:</span> www.sparkready.com.au</li>
    </ul>

    <div class="legal">license no.: 123456C<br>ABN: 12 345 678 901</div>
  </section>

  <section class="card card--back">
    <div class="feature feature--pricing">
      <div class="seal" role="img" aria-label="Gold seal with dollar sign"></div>
      <p class="feature-title">Fixed Pricing</p>
    </div>
    <div class="feature feature--time">
      <div class="seal" role="img" aria-label="Gold seal with clock"></div>
      <p class="feature-title">On Time<br>Guarantee</p>
    </div>
    <div class="feature feature--labour">
      <div class="seal" role="img" aria-label="Gold seal with wrench"></div>
      <p class="feature-title">Lifetime Labour<br>Guarantee</p>
    </div>
  </section>
</body>
</html>
```